Norvane Website Design (New Start Up Investment Management Firm)

We need a website designed. We have attached a Powerpoint with our proposed website content (which is quite minimal), the format is just a suggestion but we would like to see your alternative and improved ideas. We are a boutique investment firm so are looking for something sleek and professional. I have included on the last page of the attachment our brand colours and font styles as well as attaching our logo design. We would like the successful designer to design the website and build the buttons etc.

On the "Contact Us" page, we are open to suggestions on how best to show the map, whether is should be static or open a google maps page. We would like the phone number and email address to be set up so people can click on them on their phone and it calls us or emails us directly.

We would prefer not to have photos of landscapes on the site.
Our website is hosted on a Linux based website.

We would also like 3 links at the bottom of each page for links to pdfs:
- Disclaimer, Terms and Conditions of Web Site Use
- Stewardship
- Pillar III

Target Market(s)

Institutional Investors

Industry/Entity Type

Investment

Coding

Coded - Design and coding required

Number of Pages Required

3 page

Font styles to use
Other font styles liked:
• Logo: Lato, Text: Source Sans Pro

Colors

Designer to choose colors to be used in the design.

Requirements
Must have
• The website must use the colours and fonts on the last page of the attached powerpoint. I can't see an option to select the exact colour palette below so please look at the PPT.
• For others please see Project description.
Should not have
• Landscape photos

```html
<!DOCTYPE html>
<html lang="en">
<head>
<meta charset="utf-8">
<title>Norvane Investment Management</title>
<link rel="stylesheet" href="https://fonts.googleapis.com/css2?family=Lato:wght@400;700&display=swap">
<style>
  :root {
    --navy: #002f63;
    --ink: #0d2f5e;
    --sky: #3f8fd6;
    --sky-light: #6cb4e8;
    --nav-active: #5aa9e6;
    --white: #ffffff;
    --hero-top: #f6f7f8;
    --hero-mid: #e6edf2;
    --hero-low: #cfdbe3;
  }
  * { box-sizing: border-box; margin: 0; padding: 0; }
  html, body { width: 1200px; height: 755px; overflow: hidden; }
  body { font-family: "Lato", sans-serif; position: relative; background: var(--white); }

  .hero {
    position: absolute; left: 0; top: 0; width: 1200px; height: 632px;
  }
  .hero-backdrop {
    position: absolute; inset: 0;
    background:
      radial-gradient(ellipse at 55% 25%, var(--hero-top) 0%, rgba(246,247,248,0.9) 35%, rgba(246,247,248,0) 70%),
      linear-gradient(160deg, var(--hero-mid) 0%, var(--hero-low) 55%, var(--hero-mid) 100%);
  }

  .site-header {
    position: absolute; left: 0; top: 0; width: 1200px; height: 100px;
  }
  .brand {
    position: absolute; left: 120px; top: 28px; height: 59px;
    display: flex; align-items: center; gap: 12px;
  }
  .brand-square { width: 48px; height: 48px; background: var(--navy); }
  .brand-name {
    font-size: 46px; font-weight: 400; color: var(--navy); letter-spacing: 1px; line-height: 1;
  }
  .main-nav {
    position: absolute; top: 48px; right: 128px;
    display: flex; gap: 42px;
  }
  .main-nav a {
    font-size: 16.5px; color: var(--navy); text-decoration: none; text-transform: uppercase; line-height: 20px;
  }
  .main-nav a.is-current { color: var(--nav-active); }

  .welcome {
    position: absolute; left: 0; top: 196px; width: 1200px; text-align: center;
  }
  .welcome-title {
    font-size: 40px; font-weight: 400; color: var(--sky); letter-spacing: 0.5px; line-height: 50px;
  }
  .welcome-text {
    margin: 22px auto 0; width: 860px;
    font-size: 20px; color: var(--ink); line-height: 29px;
  }
  .read-more {
    display: inline-block; margin-top: 30px;
    width: 153px; height: 39px; line-height: 39px;
    background: var(--sky-light); color: var(--white);
    font-size: 15px; text-decoration: none; text-transform: uppercase;
  }

  .site-footer {
    position: absolute; left: 0; top: 632px; width: 1200px; height: 123px;
    background: var(--navy); color: var(--white);
  }
  .pdf-links {
    position: absolute; left: 123px; top: 30px;
    display: flex; gap: 12px; font-size: 16.5px; line-height: 20px;
  }
  .pdf-links a { color: var(--white); text-decoration: none; }
  .pdf-links .divider { opacity: 0.9; }
  .copyright {
    position: absolute; left: 123px; top: 64px; font-size: 13px; line-height: 16px;
  }
  .social {
    position: absolute; left: 886px; top: 664px - 632px;
  }
  .social-list {
    position: absolute; left: 886px; top: 32px; display: flex; gap: 5px;
  }
  .social-dot {
    width: 36px; height: 36px; border-radius: 50%; border: 1.5px solid var(--white);
  }
</style>
</head>
<body>
  <section class="hero">
    <div class="hero-backdrop" role="img" aria-label="Soft, pale upward view of glass office towers"></div>

    <header class="site-header">
      <div class="brand">
        <span class="brand-square"></span>
        <span class="brand-name">NORVANE</span>
      </div>
      <nav class="main-nav">
        <a href="#" class="is-current">Home</a>
        <a href="#">About Us</a>
        <a href="#">Approach</a>
        <a href="#">Contact Us</a>
      </nav>
    </header>

    <div class="welcome">
      <h1 class="welcome-title">WELCOME TO NORVANE</h1>
      <p class="welcome-text">Norvane Investment Management was founded in 2016 with a clear vision to create an independent and nimble firm focused on generating superior risk-adjusted returns.</p>
      <a href="#" class="read-more">Read More</a>
    </div>
  </section>

  <footer class="site-footer">
    <nav class="pdf-links">
      <a href="#">Disclaimer</a><span class="divider">|</span>
      <a href="#">Terms and Conditions</a><span class="divider">|</span>
      <a href="#">Stewardship</a><span class="divider">|</span>
      <a href="#">Pillar III</a>
    </nav>
    <p class="copyright">© 2017 Company Name&nbsp; All right reserved&nbsp; Term of Use</p>
    <div class="social-list" aria-label="Social links">
      <span class="social-dot"></span>
      <span class="social-dot"></span>
      <span class="social-dot"></span>
      <span class="social-dot"></span>
      <span class="social-dot"></span>
    </div>
  </footer>
</body>
</html>
```